Quorva - corporate Business Card

We need a good look and innovative business card for a new start up company based in Los Angeles called "Quorva". We are in a payment business, including payment card, app, and ewallet. We are expert in online payment and Card not present (CNP) transaction.
We need an innovative, modern business card.

Our logo font is Aero Matics

Target Market(s)

Startup - Bank - Online Payment - Card Manufacturing

Industry/Entity Type

Startup

Contact Information for Business Card

phone: 555 014 7396 - Address: 4172 Marlowe blvd, Brenmoor, CA 90299

Requirements
Must have
• Message: innovative, professional, expert, high tech, trust, online payment expert, security
Nice to have
• no comment
Should not have
• no Comment

```html
<!DOCTYPE html>
<html lang="en">
<head>
<meta charset="utf-8">
<title>Quorva business card</title>
<link href="https://fonts.googleapis.com/css2?family=Lato:wght@400;700&display=swap" rel="stylesheet">
<style>
  :root {
    --brand-red: #b41e2c;
    --brand-red-soft: #c54b55;
    --paper: #f7f7f7;
    --ink-white: #ffffff;
    --backdrop: #ececec;
  }
  html, body {
    margin: 0;
    padding: 0;
    width: 1200px;
    height: 586px;
    overflow: hidden;
    background: var(--backdrop);
    font-family: "Lato", Arial, sans-serif;
  }
  .canvas {
    position: relative;
    width: 1200px;
    height: 586px;
  }
  .card {
    position: absolute;
    top: 129px;
    width: 501px;
    height: 300px;
    overflow: hidden;
  }
  .card--front {
    left: 61px;
    background: var(--brand-red);
  }
  .front__disc {
    position: absolute;
    left: 275px;
    top: 23px;
    width: 260px;
    height: 260px;
    border-radius: 50%;
    background: var(--brand-red-soft);
  }
  .front__name {
    position: absolute;
    left: 30px;
    top: 206px;
    margin: 0;
    font-size: 38px;
    font-weight: 700;
    color: var(--ink-white);
    line-height: 1;
  }
  .front__web {
    position: absolute;
    left: 32px;
    top: 261px;
    margin: 0;
    font-size: 11.5px;
    font-weight: 700;
    letter-spacing: 2.6px;
    color: var(--ink-white);
  }
  .card--back {
    left: 619px;
    background: var(--paper);
  }
  .back__stripe {
    position: absolute;
    top: 0;
    height: 300px;
    background: var(--brand-red);
  }
  .back__stripe--one { left: 242px; width: 4px; }
  .back__stripe--two { left: 249px; width: 4px; }
  .back__panel {
    position: absolute;
    left: 254px;
    top: 0;
    width: 247px;
    height: 300px;
    background: var(--brand-red);
  }
  .brand {
    position: absolute;
    left: 34px;
    top: 127px;
    display: flex;
    align-items: center;
    gap: 6px;
  }
  .brand__dot {
    width: 54px;
    height: 54px;
    border-radius: 50%;
    background: var(--brand-red);
  }
  .brand__name {
    font-size: 35px;
    font-weight: 700;
    color: var(--brand-red);
    line-height: 1;
  }
  .contact {
    position: absolute;
    left: 286px;
    top: 0;
    color: var(--ink-white);
  }
  .contact__name {
    position: absolute;
    top: 76px;
    margin: 0;
    font-size: 17px;
    font-weight: 700;
    white-space: nowrap;
  }
  .contact__role {
    position: absolute;
    top: 99px;
    margin: 0;
    font-size: 11.5px;
    white-space: nowrap;
  }
  .contact__address {
    position: absolute;
    top: 136px;
    margin: 0;
    font-size: 12.5px;
    font-weight: 700;
    line-height: 17px;
    font-style: normal;
    white-space: nowrap;
  }
  .contact__line {
    position: absolute;
    display: flex;
    align-items: center;
    gap: 7px;
    margin: 0;
    font-size: 12.5px;
    white-space: nowrap;
  }
  .contact__line--phone { top: 189px; }
  .contact__line--email { top: 214px; }
  .contact__icon { width: 17px; height: 17px; }
</style>
</head>
<body>
<main class="canvas">
  <section class="card card--front" aria-label="Card front">
    <div class="front__disc"></div>
    <h1 class="front__name">quorva</h1>
    <p class="front__web">www.quorvawebsite.com</p>
  </section>

  <section class="card card--back" aria-label="Card back">
    <div class="brand">
      <span class="brand__dot"></span>
      <span class="brand__name">quorva</span>
    </div>
    <div class="back__stripe back__stripe--one"></div>
    <div class="back__stripe back__stripe--two"></div>
    <div class="back__panel"></div>
    <div class="contact">
      <h2 class="contact__name">Marcus Hale</h2>
      <p class="contact__role">Owner &amp; Founder</p>
      <address class="contact__address">4172 Marlowe blvd,<br>Brenmoor, CA 90299</address>
      <p class="contact__line contact__line--phone">
        <svg class="contact__icon" viewBox="0 0 20 20" aria-hidden="true">
          <circle cx="10" cy="10" r="10" fill="#fff"/>
          <path d="M5 8.5c0-1.5 2.2-2.5 5-2.5s5 1 5 2.5l-1.8.6-.6-1.3c-1.7-.5-3.5-.5-5.2 0l-.6 1.3z M6.5 10.5h7l.8 3.5h-8.6z" fill="#b41e2c"/>
        </svg>
        (555) 014-7396
      </p>
      <p class="contact__line contact__line--email">
        <svg class="contact__icon" viewBox="0 0 20 20" aria-hidden="true">
          <circle cx="10" cy="10" r="10" fill="#fff"/>
          <rect x="5" y="6.5" width="10" height="7" fill="#b41e2c"/>
          <path d="M5 6.5l5 4 5-4" fill="none" stroke="#fff" stroke-width="1"/>
        </svg>
        MarcusH@quorvaweb.com
      </p>
    </div>
  </section>
</main>
</body>
</html>
```